Brandwyn Fuel Retro Website Design

Have a logo. Need a website design to go along with the logo design. Full Design Specs are here: https://files.plinverdocs.net/sheet/d/8QmRtZxWv3-41pk527LNB_XY4HaPcOdsuw2K-rb6/view

Target Market(s)

Independent Gas Station Owners

Number of Pages Required

1 page

Font styles to use
Sans Serif

Colors

Designer to choose colors to be used in the design.

```html
<!DOCTYPE html>
<html lang="en">
<head>
<meta charset="utf-8">
<title>Brandwyn Fuel</title>
<link href="https://fonts.googleapis.com/css2?family=Libre+Baskerville:wght@400;700&family=Roboto:ital,wght@0,400;0,500;0,700;1,400&display=swap" rel="stylesheet">
<style>
:root{
  --red:#e3212b;
  --ink:#1f1f1f;
  --text:#666;
  --page:#e2e2e2;
  --header:#e9e9e9;
  --services:#bfbfbf;
  --footer:#555;
  --white:#fff;
  --serif:"Libre Baskerville",Georgia,serif;
  --sans:"Roboto",Arial,sans-serif;
}
*{box-sizing:border-box;margin:0;padding:0}
html,body{width:1200px;height:3389px;overflow:hidden}
body{position:relative;background:var(--page);font-family:var(--sans);color:var(--ink)}
.abs{position:absolute}
/* header */
.site-header{left:0;top:0;width:1200px;height:130px;background:var(--header);border-bottom:5px solid var(--white);z-index:3}
.brand{left:140px;top:40px;display:flex;align-items:center;gap:12px}
.brand-dot{width:44px;height:44px;border-radius:50%;background:var(--red)}
.brand-name{font-family:var(--sans);font-weight:700;font-size:26px;color:var(--ink);letter-spacing:1px}
.main-nav{left:485px;top:56px;display:flex;gap:24px;font-weight:500;font-size:15px;text-transform:uppercase}
.search-icon{left:1040px;top:58px}
/* hero */
.hero-photo{left:0;top:130px;width:1200px;height:640px;background:linear-gradient(180deg,#b9bcc0 0%,#9c9a96 45%,#7d7b78 75%,#8a8a88 100%)}
.hero-title{left:0;top:388px;width:1200px;text-align:center;font-family:var(--serif);font-weight:700;font-size:52px;color:var(--white);letter-spacing:3px}
.hero-sub{left:340px;top:460px;width:520px;text-align:center;font-weight:700;font-size:16.5px;line-height:25px;color:var(--white)}
.btn{display:inline-block;background:var(--red);color:var(--white);font-weight:700;font-size:16px;text-transform:uppercase;border-radius:24px;text-align:center}
.hero-btn{left:515px;top:532px;width:171px;height:46px;line-height:46px}
/* about */
.about-bg-word{left:-190px;top:950px;width:480px;transform:rotate(-90deg);font-family:var(--serif);font-weight:700;font-size:62px;color:rgba(0,0,0,.06);white-space:nowrap;text-align:center}
.section-title{font-family:var(--serif);font-weight:700;font-size:38px;color:var(--ink)}
.about-title{left:146px;top:862px}
.about-copy{left:146px;top:940px;width:440px;font-size:14px;line-height:28px;color:var(--text)}
.about-copy p{margin-bottom:18px}
.about-btn{left:146px;top:1167px;width:176px;height:47px;line-height:47px}
.about-shapes{left:0;top:770px}
/* services */
.services{left:0;top:1317px;width:1200px;height:686px;background:var(--services)}
.heading-wrap{left:0;width:1200px;height:90px;text-align:center}
.ghost{position:absolute;left:0;width:1200px;text-align:center;font-family:var(--serif);font-weight:700;font-size:76px;color:rgba(0,0,0,.08);top:-12px;white-space:nowrap}
.heading-wrap .section-title{position:relative;top:8px}
.card{top:1508px;width:276px;height:376px;background:var(--white)}
.card-img{width:272px;height:182px;margin:2px 2px 0}
.card-icon{position:absolute;left:106px;top:152px;width:64px;height:64px;border-radius:50%;background:var(--white);display:flex;align-items:center;justify-content:center}
.card h3{margin-top:46px;text-align:center;font-weight:500;font-size:20px}
.card p{margin:14px 18px 0;text-align:center;font-size:13.5px;line-height:24px;color:var(--text)}
.card .pill{position:absolute;left:72px;top:357px;width:132px;height:36px;line-height:36px;border-radius:18px;font-weight:700;font-size:14px;text-align:center;background:var(--white);color:var(--red);box-shadow:0 1px 3px rgba(0,0,0,.15)}
.card .pill.active{background:var(--red);color:var(--white)}
.round-arrow{width:30px;height:30px;border-radius:50%;background:var(--red);display:flex;align-items:center;justify-content:center}
/* testimonials */
.testi{top:2200px;width:290px}
.avatar{position:absolute;left:0;top:10px;width:60px;height:60px;border-radius:50%;background:linear-gradient(160deg,#cfc7c2,#8e8580);border:3px solid var(--white)}
.quote-mark{position:absolute;left:22px;top:62px;width:16px;height:16px;border-radius:50%;background:var(--red)}
.testi-body{position:absolute;left:74px;top:12px;width:216px}
.stars{color:#f5a623;font-size:13px;letter-spacing:1px}
.testi-body blockquote{margin-top:6px;font-style:italic;font-size:11.5px;line-height:21.5px;color:var(--text);text-align:justify}
.testi-name{position:absolute;left:0;top:137px;font-weight:500;font-size:12.5px;text-transform:uppercase}
.testi-role{position:absolute;left:0;top:160px;font-size:11px;color:var(--text)}
.dots{left:563px;top:2413px;display:flex;gap:5px}
.dots span{width:10px;height:10px;border-radius:50%;border:1px solid #999}
.dots span.on{background:var(--red);border-color:var(--red)}
.divider{left:144px;top:2522px;width:912px;height:1px;background:#c8c8c8}
.partners-copy{left:240px;top:2680px;width:720px;text-align:center;font-size:13.5px;line-height:26px;color:var(--text)}
.badge{top:2773px;width:171px;height:75px;background:var(--white);display:flex;align-items:center;justify-content:center}
.badge span{display:block;width:110px;height:26px;border-radius:4px;background:#cfcfcf}
.badge.on{border-bottom:3px solid var(--red)}
/* footer */
.footer-shape{left:0;top:2930px}
.footer-col{top:3098px;color:var(--white)}
.footer-col h4{font-weight:500;font-size:15px;text-transform:uppercase;margin-bottom:18px}
.footer-col li{list-style:none;font-size:13px;line-height:24px;padding-left:22px;position:relative}
.footer-col li::before{content:"»";position:absolute;left:0;top:-1px;font-size:14px}
.contact-item{position:relative;padding-left:30px;font-size:13px;line-height:19px;margin-bottom:24px}
.contact-item svg{position:absolute;left:0;top:2px}
.news-form{left:787px;top:3134px;width:268px;height:32px;border-radius:16px;background:var(--white);border:2px solid #ddd}
.news-form span{position:absolute;left:14px;top:7px;font-size:11px;color:#999}
.news-form b{position:absolute;right:2px;top:2px;width:92px;height:24px;border-radius:12px;background:var(--red);color:var(--white);font-size:12px;line-height:24px;text-align:center}
.social{left:793px;top:3186px;display:flex;gap:11px}
.social span{width:30px;height:30px;border-radius:50%;border:1.5px solid var(--white)}
.footer-line{left:144px;top:3318px;width:912px;height:1px;background:#888}
.copyright{left:0;top:3346px;width:1200px;text-align:center;font-size:14px;color:var(--white)}
</style>
</head>
<body>

<header class="site-header abs">
  <div class="brand abs"><span class="brand-dot"></span><span class="brand-name">BRANDWYN FUEL</span></div>
  <nav class="main-nav abs"><span>Home</span><span>About Us</span><span>Products &amp; Services</span><span>More</span><span>Contact Us</span></nav>
  <svg class="search-icon abs" width="16" height="16" viewBox="0 0 16 16"><circle cx="6.5" cy="6.5" r="5" fill="none" stroke="#1f1f1f" stroke-width="2"/><path d="M10.5 10.5L15 15" stroke="#1f1f1f" stroke-width="2.4"/></svg>
</header>

<section>
  <div class="hero-photo abs" role="img" aria-label="Photo of the fuel company's white metal building with pickup trucks parked in front"></div>
  <svg class="abs" style="left:0;top:640px" width="1200" height="135" viewBox="0 0 1200 135">
    <path d="M0 14 C 300 110, 900 110, 1200 14 L1200 135 L0 135 Z" fill="#e2e2e2"/>
    <path d="M0 14 C 300 110, 900 110, 1200 14 C 900 92, 300 92, 0 14 Z" fill="#fff"/>
    <path d="M90 40 C 380 150, 820 150, 1110 40 C 820 128, 380 128, 90 40 Z" fill="#e3212b"/>
  </svg>
  <h1 class="hero-title abs">BRANDWYN FUEL</h1>
  <p class="hero-sub abs">Lorem ipsum dolor site consectetur adipiscing labore et dolore eiusmod tempor incididunt labore.</p>
  <span class="btn hero-btn abs">Read More &#10140;</span>
</section>

<section>
  <svg class="about-shapes abs" width="1200" height="547" viewBox="0 0 1200 547">
    <circle cx="1070" cy="490" r="285" fill="#e3212b"/>
  </svg>
  <div class="about-bg-word abs">BRANDWYN FUEL</div>
  <h2 class="section-title about-title abs">ABOUT BRANDWYN FUEL</h2>
  <div class="about-copy abs">
    <p>Brandwyn Fuel provides the full-scale service of a petroleum distributor, delivering gasoline, diesel and lube oils to retail, commercial and farm accounts.&nbsp; Our own fleet of delivery trucks provides distribution of fuel to several counties within the North Texas area.</p>
    <p>Along with a knowledgeable and professional staff, Brandwyn Fuel makes customer service and satisfaction priority one.</p>
  </div>
  <span class="btn about-btn abs">Contact Us &#10140;</span>
  <div class="abs" style="left:689px;top:858px;width:368px;height:368px;border-radius:50%;background:linear-gradient(150deg,#c9c4bb,#5b6a86 55%,#3d3a38)" role="img" aria-label="Photo of store shelves stocked with motor oil bottles"></div>
</section>

<section>
  <div class="services abs"></div>
  <div class="heading-wrap abs" style="top:1400px"><div class="ghost">OUR SERVICES</div><h2 class="section-title">OUR SERVICES</h2></div>

  <div class="round-arrow abs" style="left:57px;top:1681px"><svg width="10" height="12" viewBox="0 0 10 12"><path d="M7 1L2 6l5 5" fill="none" stroke="#fff" stroke-width="2"/></svg></div>
  <div class="round-arrow abs" style="left:1113px;top:1681px"><svg width="10" height="12" viewBox="0 0 10 12"><path d="M3 1l5 5-5 5" fill="none" stroke="#fff" stroke-width="2"/></svg></div>

  <article class="card abs" style="left:144px">
    <div class="card-img" style="background:linear-gradient(180deg,#cfd2d4,#7b8aa6 60%,#6e6c68)" role="img" aria-label="Photo of fuel delivery trucks"></div>
    <div class="card-icon"><svg width="40" height="30" viewBox="0 0 40 30" fill="none" stroke="#e3212b" stroke-width="1.8"><rect x="2" y="8" width="22" height="14" rx="7"/><path d="M24 12h8l5 6v4H24"/><circle cx="9" cy="24" r="3.5"/><circle cx="31" cy="24" r="3.5"/></svg></div>
    <h3>FUEL DELIVERY</h3>
    <p>Sed ut perspiciatis unde omnis natus error sit voluptatem accusantium doloremque laudantium totam rem</p>
    <span class="pill">READ MORE &#10140;</span>
  </article>
  <article class="card abs" style="left:461px">
    <div class="card-img" style="background:linear-gradient(180deg,#d7d9db,#8a8f95 45%,#6d6f70)" role="img" aria-label="Photo of a gray steel cargo container"></div>
    <div class="card-icon"><svg width="40" height="36" viewBox="0 0 40 36" fill="none" stroke="#e3212b" stroke-width="1.8"><path d="M20 2v8M12 10h16"/><rect x="4" y="14" width="32" height="18"/><path d="M9 18v10M14 18v10M19 18v10M24 18v10M29 18v10"/></svg></div>
    <h3>CARGO CONTAINERS</h3>
    <p>Sed ut perspiciatis unde omnis natus error sit voluptatem accusantium doloremque laudantium totam rem</p>
    <span class="pill active">READ MORE &#10140;</span>
  </article>
  <article class="card abs" style="left:780px">
    <div class="card-img" style="background:linear-gradient(180deg,#bfc0c0,#e9e9e9 45%,#8c8a86)" role="img" aria-label="Photo of white farm fuel storage tanks"></div>
    <div class="card-icon"><svg width="40" height="36" viewBox="0 0 40 36" fill="none" stroke="#e3212b" stroke-width="1.8"><circle cx="14" cy="20" r="9"/><path d="M8 30h12M14 11V5M26 34V14h8v20"/></svg></div>
    <h3>FARM FUEL</h3>
    <p>Sed ut perspiciatis unde omnis natus error sit voluptatem accusantium doloremque laudantium totam rem</p>
    <span class="pill">READ MORE &#10140;</span>
  </article>
</section>

<section>
  <div class="heading-wrap abs" style="top:2104px"><div class="ghost">TESTIMONIALS</div><h2 class="section-title">OUR TESTIMONIALS</h2></div>
  <svg class="abs" style="left:80px;top:2268px" width="12" height="20" viewBox="0 0 12 20"><path d="M10 2L2 10l8 8" fill="none" stroke="#888" stroke-width="2"/></svg>
  <svg class="abs" style="left:1106px;top:2268px" width="12" height="20" viewBox="0 0 12 20"><path d="M2 2l8 8-8 8" fill="none" stroke="#888" stroke-width="2"/></svg>

  <div class="testi abs" style="left:144px">
    <div class="avatar" role="img" aria-label="Customer portrait"></div><span class="quote-mark"></span>
    <div class="testi-body"><div class="stars">★★★★★</div><blockquote>“ At vero eos et accusamus et iustodio dignissimos ducimus qui blanditiipraesnt ium voluptatum deleniti atque corrupti quos dolores quas molestias ”</blockquote></div>
    <div class="testi-name" style="left:74px">Marla Quinby</div><div class="testi-role" style="left:74px">Creative Manager, USA</div>
  </div>
  <div class="testi abs" style="left:464px">
    <div class="avatar" role="img" aria-label="Customer portrait"></div><span class="quote-mark"></span>
    <div class="testi-body"><div class="stars">★★★★★</div><blockquote>“ At vero eos et accusamus et iustodio dignissimos ducimus qui blanditiipraesnt ium voluptatum deleniti atque corrupti quos dolores quas molestias ”</blockquote></div>
    <div class="testi-name" style="left:74px">Devon Ashcroft</div><div class="testi-role" style="left:74px">Events Manager, USA</div>
  </div>
  <div class="testi abs" style="left:780px">
    <div class="avatar" role="img" aria-label="Customer portrait"></div><span class="quote-mark"></span>
    <div class="testi-body"><div class="stars">★★★★★</div><blockquote>“ At vero eos et accusamus et iustodio dignissimos ducimus qui blanditiipraesnt ium voluptatum deleniti atque corrupti quos dolores quas molestias ”</blockquote></div>
    <div class="testi-name" style="left:74px">Pieter Lunde</div><div class="testi-role" style="left:74px">Task Manager, USA</div>
  </div>
  <div class="dots abs"><span></span><span></span><span class="on"></span><span></span><span></span></div>
  <div class="divider abs"></div>
</section>

<section>
  <div class="heading-wrap abs" style="top:2600px"><div class="ghost">PARTNERS</div><h2 class="section-title">OUR PARTNERS</h2></div>
  <p class="partners-copy abs">Lorem ipsum dolor sit amet, consectetur adipiscing elit, sed do eiusmod tempor incididunt ut labore et dolore magna aliqua. Ut enim ad minim veniam, quis nostrud exercitation ullamco laboris nisi ut aliquip.</p>
  <svg class="abs" style="left:92px;top:2800px" width="12" height="20" viewBox="0 0 12 20"><path d="M10 2L2 10l8 8" fill="none" stroke="#888" stroke-width="2"/></svg>
  <svg class="abs" style="left:1097px;top:2800px" width="12" height="20" viewBox="0 0 12 20"><path d="M2 2l8 8-8 8" fill="none" stroke="#888" stroke-width="2"/></svg>
  <div class="badge abs" style="left:142px"><span></span></div>
  <div class="badge abs" style="left:328px"><span></span></div>
  <div class="badge on abs" style="left:514px"><span></span></div>
  <div class="badge abs" style="left:700px"><span></span></div>
  <div class="badge abs" style="left:886px"><span></span></div>
</section>

<footer>
  <svg class="footer-shape abs" width="1200" height="459" viewBox="0 0 1200 459">
    <path d="M0 130 C 300 10, 900 10, 1200 130 L1200 459 L0 459 Z" fill="#555"/>
    <path d="M0 130 C 300 10, 900 10, 1200 130 C 900 30, 300 30, 0 130 Z" fill="#fff"/>
    <path d="M90 100 C 380 -10, 820 -10, 1110 100 C 820 20, 380 20, 90 100 Z" fill="#e3212b"/>
  </svg>
  <div class="footer-col abs" style="left:143px"><h4>Quick Links</h4><ul><li>Home</li><li>About Us</li><li>Services</li><li>B's Containers</li><li>Employment</li><li>Contact Us</li></ul></div>
  <div class="footer-col abs" style="left:326px"><h4>Other Links</h4><ul><li>Reviews</li><li>Management</li><li>Blog Post</li><li>Help</li><li>FAQ</li><li>Terms of Use</li></ul></div>
  <div class="footer-col abs" style="left:537px"><h4>Contact Us</h4>
    <div class="contact-item"><svg width="12" height="16" viewBox="0 0 12 16"><path d="M6 0a6 6 0 0 1 6 6c0 4-6 10-6 10S0 10 0 6a6 6 0 0 1 6-6z" fill="#fff"/><circle cx="6" cy="6" r="2.2" fill="#555"/></svg>48 Depot Lane, Fairvale,<br>North State, USA.</div>
    <div class="contact-item"><svg width="14" height="14" viewBox="0 0 14 14"><path d="M3 0l3 3-2 2c1 2 3 4 5 5l2-2 3 3-2 3C6 14 0 8 0 3z" fill="#fff"/></svg>(+10 555 014 2277</div>
    <div class="contact-item"><svg width="14" height="12" viewBox="0 0 14 12"><rect width="14" height="12" rx="1" fill="#fff"/><path d="M0 1l7 5 7-5" fill="none" stroke="#555" stroke-width="1.4"/></svg>info@brandwynfuel.com</div>
  </div>
  <div class="footer-col abs" style="left:789px"><h4>Newsletter Sign Up</h4></div>
  <div class="news-form abs"><span>Email address</span><b>Subscribe</b></div>
  <div class="social abs"><span></span><span></span><span></span><span></span><span></span></div>
  <div class="footer-line abs"></div>
  <p class="copyright abs">© Copyright 2019 Brandwyn Fuel. All Rights Reserved &nbsp;&nbsp; | &nbsp;&nbsp; Privacy Policy</p>
</footer>

</body>
</html>
```